Verdant Systems Business Card

want the back of card to be blue- with the logo in the center
front of card- info plus logo (info being mailing address, email address, and website address )
4 different names with titles to have on cards
1) Calvin Borsted - Owner
2) Naomi Trelvik- Customer Relationship Specialist
3) Felix Andrade- Vice President of Sales
4) Owen Markby- Chief Technology Officer

Target Market(s)

tech company in the government/probation office industry

Industry/Entity Type

Government Office

Contact Information for Business Card

1) Calvin Borsted - Owner

Colors
0355a3
ffffff

Requirements
Must have
• back side should be blue, with the logo placed in the center
• front side needs to include both the logo, as well as company info (info should include website address, email address, and mailing address)

```html
<!DOCTYPE html>
<html lang="en">
<head>
<meta charset="utf-8">
<title>Verdant Systems Business Card</title>
<link href="https://fonts.googleapis.com/css2?family=PT+Serif:wght@400&family=Roboto:wght@400&display=swap" rel="stylesheet">
<style>
  :root {
    --navy: #283a63;
    --paper: #ffffff;
    --ink-grey: #6f7078;
    --mark-tint: #e3e6ee;
    --backdrop: #a4a1a2;
    --backdrop-light: #b3b0b1;
  }
  html, body {
    margin: 0;
    padding: 0;
    width: 1200px;
    height: 1200px;
    overflow: hidden;
  }
  .canvas {
    position: relative;
    width: 1200px;
    height: 1200px;
    background: radial-gradient(ellipse at 50% 40%, var(--backdrop-light), var(--backdrop));
  }
  .card {
    position: absolute;
    width: 714px;
    height: 422px;
    border-radius: 22px;
    overflow: hidden;
  }
  .card-back {
    left: 238px;
    top: 117px;
    background: var(--navy);
  }
  .card-front {
    left: 231px;
    top: 646px;
    background: var(--paper);
  }
  .brand-disc {
    position: absolute;
    border-radius: 50%;
  }
  .card-back .brand-disc {
    left: 167px;
    top: 11px;
    width: 400px;
    height: 400px;
    background: rgba(255, 255, 255, 0.05);
  }
  .card-front .brand-disc {
    left: -30px;
    top: 30px;
    width: 340px;
    height: 340px;
    background: var(--mark-tint);
  }
  .wordmark {
    position: absolute;
    font-family: "PT Serif", Georgia, serif;
    font-weight: 400;
    text-transform: uppercase;
    white-space: nowrap;
    margin: 0;
  }
  .card-back .wordmark {
    left: 0;
    right: 0;
    top: 180px;
    text-align: center;
    color: var(--paper);
    font-size: 50px;
    letter-spacing: 2px;
  }
  .card-front .wordmark {
    right: 32px;
    top: 48px;
    color: var(--navy);
    font-size: 30px;
    letter-spacing: 1px;
  }
  .edge-tab {
    position: absolute;
    right: -14px;
    top: 178px;
    width: 30px;
    height: 78px;
    border-radius: 40px 0 0 40px;
    background: var(--navy);
  }
  .person {
    position: absolute;
    right: 32px;
    top: 188px;
    text-align: right;
  }
  .person-name {
    font-family: "PT Serif", Georgia, serif;
    font-size: 25px;
    color: var(--navy);
    text-transform: uppercase;
    letter-spacing: 0.5px;
    margin: 0;
  }
  .person-title {
    font-family: "Roboto", Arial, sans-serif;
    font-size: 17px;
    color: var(--ink-grey);
    margin: 4px 0 0;
  }
  .contact {
    position: absolute;
    right: 29px;
    top: 280px;
    list-style: none;
    margin: 0;
    padding: 0;
    font-family: "Roboto", Arial, sans-serif;
    font-size: 17px;
    color: var(--ink-grey);
    text-align: right;
  }
  .contact li {
    display: flex;
    justify-content: flex-end;
    align-items: center;
    gap: 12px;
    height: 26px;
  }
  .contact svg {
    width: 16px;
    height: 16px;
    fill: var(--navy);
  }
  .contact .address {
    margin-top: 6px;
  }
</style>
</head>
<body>
<main class="canvas">
  <section class="card card-back" aria-label="Card back">
    <div class="brand-disc" aria-hidden="true"></div>
    <p class="wordmark">Verdant Systems</p>
  </section>

  <section class="card card-front" aria-label="Card front">
    <div class="brand-disc" aria-hidden="true"></div>
    <p class="wordmark">Verdant Systems</p>
    <div class="edge-tab"></div>
    <div class="person">
      <p class="person-name">Naomi Trelvik</p>
      <p class="person-title">Customer Relationship Specialist</p>
    </div>
    <ul class="contact">
      <li>111-111-1111
        <svg viewBox="0 0 16 16" aria-hidden="true"><path d="M1 5c0-2 3-3 7-3s7 1 7 3v1.5h-3.5V5H4.5v1.5H1z M3 8l2-2h6l2 2v6H3z M6 9h4v3H6z"/></svg>
      </li>
      <li>naomi.t@verdantsystems.com
        <svg viewBox="0 0 16 16" aria-hidden="true"><path d="M1 3h14v10H1z M2.5 4.2 8 8.6l5.5-4.4z" fill-rule="evenodd"/></svg>
      </li>
      <li>www.verdantsystems.com
        <svg viewBox="0 0 16 16" aria-hidden="true"><path d="M8 1a7 7 0 1 0 0 14A7 7 0 0 0 8 1zm0 1.4c.9 0 1.9 1.8 2.1 4.6H5.9C6.1 4.2 7.1 2.4 8 2.4zM5.9 9h4.2c-.2 2.8-1.2 4.6-2.1 4.6S6.1 11.8 5.9 9zM2.5 7a5.6 5.6 0 0 1 2.6-3.9A10 10 0 0 0 4.4 7zm0 2h1.9c.1 1.5.3 2.8.7 3.9A5.6 5.6 0 0 1 2.5 9zm9.1 0h1.9a5.6 5.6 0 0 1-2.6 3.9c.4-1.1.6-2.4.7-3.9zm0-2c-.1-1.5-.3-2.8-.7-3.9A5.6 5.6 0 0 1 13.5 7z"/></svg>
      </li>
      <li class="address">234 Anywhere St., Any City, Town, US 123456</li>
    </ul>
  </section>
</main>
</body>
</html>
```